Tobias Ränkel and Co stationary design

Name of business:
Tobias Ränkel and Co

Can be written as:
Tobias Ränkel and Co
Tobias Ränkel & Co
tobias ränkel & co

If broken into letters:
TR&Co
tr&co

We are a Railway Safety Training Company
Our focus is on rail safety, Rail Management, Safety Management, Train Control Training, Accident Investigation.

.

Project Deadline Extended Reason: The original date was set to commence as soon as the logo contest finished. Sketch harbor started the project as soon as it was paid. Added Thursday, May 12, 2016

Target Market(s)

Professionals, CEO's and Managing Directors

Industry/Entity Type

Management Consulting

Font styles to use
Sans Serif

Requirements
Must have
• Professional, Sharp, Creative and modern
• Please note that this is for stationary concept which must include
• - business card
• - letterhead
• - envelope
• - with compliments slip
• - document cover (like book or folder cover)
• - dividers for folders....
• These must all have a common theme or style
Nice to have
• Keep if fresh
Should not have
• Please don't sent just fonts.... Must be creative

```html
<!DOCTYPE html>
<html lang="en">
<head>
<meta charset="utf-8">
<title>TR &amp; Co. Business Card</title>
<link href="https://fonts.googleapis.com/css2?family=Open+Sans:wght@400;600;700&display=swap" rel="stylesheet">
<style>
  :root {
    --bg: #e9e6e1;
    --red: #d0132f;
    --red-dark: #a80a22;
    --navy: #1b2f68;
    --white: #ffffff;
    --ink: #1b2f68;
  }
  * { margin: 0; padding: 0; box-sizing: border-box; }
  html, body {
    width: 1200px; height: 843px; overflow: hidden;
    background: var(--bg);
    font-family: "Open Sans", Arial, sans-serif;
  }
  .stage {
    position: relative; width: 1200px; height: 843px;
    display: flex; align-items: center; justify-content: center; gap: 40px;
  }
  .card {
    position: relative; width: 540px; height: 309px;
    border-radius: 4px; overflow: hidden;
    box-shadow: 0 10px 24px rgba(0,0,0,0.18);
  }
  /* Back side */
  .card-back {
    background: linear-gradient(135deg, var(--red) 0%, var(--red-dark) 100%);
    color: var(--white);
  }
  .back-mark {
    position: absolute; left: 0; right: 0; top: 98px;
    display: flex; align-items: center; justify-content: center; gap: 14px;
  }
  .back-dot { width: 22px; height: 22px; border-radius: 50%; background: var(--white); }
  .back-name { font-size: 44px; line-height: 56px; font-weight: 700; letter-spacing: 0.5px; }
  .back-web {
    position: absolute; left: 0; right: 0; top: 196px;
    text-align: center; font-size: 13px; letter-spacing: 3px;
  }
  /* Front side */
  .card-front { background: var(--white); }
  .band { position: absolute; left: 0; top: 0; width: 540px; height: 309px; }
  .front-mark {
    position: absolute; top: 62px; left: 0; right: 0;
    display: flex; align-items: center; justify-content: center; gap: 12px;
  }
  .front-dot { width: 18px; height: 18px; border-radius: 50%; background: var(--red); }
  .front-name { font-size: 40px; line-height: 52px; font-weight: 700; color: var(--ink); }
  .details {
    position: absolute; left: 0; right: 0; top: 196px;
    display: flex; align-items: flex-start; color: var(--white);
  }
  .person {
    width: 270px; padding-right: 22px; text-align: right;
    font-size: 13px; line-height: 17px;
  }
  .person-name { font-size: 16px; line-height: 20px; font-weight: 600; letter-spacing: 0.5px; }
  .divider { width: 1px; height: 84px; background: rgba(255,255,255,0.7); }
  .contacts { padding-left: 22px; font-size: 13px; line-height: 20px; list-style: none; }
  .contacts li { display: flex; align-items: center; gap: 9px; white-space: nowrap; }
  .contacts svg { width: 13px; height: 13px; fill: var(--white); flex: none; }
</style>
</head>
<body>
<main class="stage">
  <section class="card card-back">
    <div class="back-mark">
      <span class="back-dot"></span>
      <span class="back-name">TR &amp; Co.</span>
    </div>
    <p class="back-web">www.trcorail.com</p>
  </section>

  <section class="card card-front">
    <svg class="band" viewBox="0 0 540 309" aria-hidden="true">
      <path d="M0 146 Q250 158 540 198" fill="none" stroke="var(--red)" stroke-width="3"/>
      <path d="M0 155 Q250 166 540 206 L540 309 L0 309 Z" fill="var(--navy)"/>
    </svg>
    <div class="front-mark">
      <span class="front-dot"></span>
      <span class="front-name">TR &amp; Co.</span>
    </div>
    <div class="details">
      <div class="person">
        <p class="person-name">JONAS WEBER</p>
        <p>CEO/FOUNDER</p>
        <p>4210 Larchwood Road</p>
        <p>Fairbanks, Alaska 34190</p>
      </div>
      <div class="divider"></div>
      <ul class="contacts">
        <li><svg viewBox="0 0 16 16"><path d="M3 1h3l1.5 4-2 1.3a9 9 0 0 0 4.2 4.2L11 8.5l4 1.5v3a2 2 0 0 1-2 2A12 12 0 0 1 1 3a2 2 0 0 1 2-2z"/></svg>612 408 2715</li>
        <li><svg viewBox="0 0 16 16"><path d="M4 0h8a1 1 0 0 1 1 1v14a1 1 0 0 1-1 1H4a1 1 0 0 1-1-1V1a1 1 0 0 1 1-1zm1 2v10h6V2zm3 11a1 1 0 1 0 0 2 1 1 0 0 0 0-2z"/></svg>847 351 6028</li>
        <li><svg viewBox="0 0 16 16"><path d="M4 0h8v5H4zM1 6h14v7h-3v3H4v-3H1zm4 5v3h6v-3z"/></svg>493 720 1856</li>
        <li><svg viewBox="0 0 16 16"><path d="M0 3h16v10H0zm1.5 1.2v.3L8 9l6.5-4.5v-.3z"/></svg>hello@trcorail.com</li>
      </ul>
    </div>
  </section>
</main>
</body>
</html>
```